Copperleaf Roofing Business Card

This is my current business card. But I’d like to make some changes. Somewhere on the card I’d like to list some of the services we offer. Maybe on the back? But I’d still like to keep the red. White and black modern look.

-residential & commercial roofing
-Roof Repairs & Maintenance
-Storm Damage & Insurance Claims specialist
-Christmas Lights and permanent Christmas lights
Fencing. Windows. Gutters. Siding. Sheetrock, painting.

```html
<!DOCTYPE html>
<html lang="en">
<head>
<meta charset="utf-8">
<title>Copperleaf Roofing Co. — Business Card</title>
<link rel="stylesheet" href="https://fonts.googleapis.com/css2?family=Lato:wght@400;700;900&family=Michroma&display=swap">
<style>
  :root {
    --red: #e30613;
    --red-deep: #9e0a12;
    --black: #0b0b0b;
    --white: #ffffff;
    --ink: #161616;
    --stage: #d9d9d9;
  }
  * { box-sizing: border-box; margin: 0; padding: 0; }
  html, body {
    width: 1200px; height: 694px; overflow: hidden;
    background: var(--stage);
    font-family: "Lato", Arial, sans-serif;
  }
  .sheet {
    width: 1200px; height: 694px;
    display: flex; align-items: center; justify-content: center; gap: 30px;
  }
  .card {
    width: 555px; height: 318px; border-radius: 22px;
    position: relative; overflow: hidden;
  }

  /* Back side */
  .card--back { background: var(--black); color: var(--white); }
  .back-brand {
    position: absolute; left: 28px; top: 0; bottom: 0; width: 200px;
    display: flex; flex-direction: column; align-items: center; justify-content: center; gap: 18px;
  }
  .brand-mark {
    width: 120px; height: 120px; border-radius: 50%;
    background: radial-gradient(circle at 40% 40%, var(--red), var(--red-deep));
    border: 3px solid var(--white);
  }
  .wordmark {
    font-family: "Lato", Arial, sans-serif; font-weight: 900;
    text-transform: uppercase; letter-spacing: 1px; line-height: 1.05; text-align: center;
  }
  .card--back .wordmark { color: var(--white); font-size: 21px; }
  .divider {
    position: absolute; left: 245px; top: 40px; bottom: 40px; width: 2px;
    background: linear-gradient(to bottom, transparent, var(--red) 30%, var(--red) 70%, transparent);
  }
  .services {
    position: absolute; left: 272px; right: 22px; top: 50%; transform: translateY(-50%);
    list-style: none; font-size: 15.5px; line-height: 1.42;
  }
  .services li { position: relative; padding-left: 16px; }
  .services li::before {
    content: ""; position: absolute; left: 0; top: 8px;
    width: 7px; height: 7px; border-radius: 50%; background: var(--red);
  }

  /* Front side */
  .card--front { background: var(--white); color: var(--ink); }
  .front-brand {
    position: absolute; left: 34px; top: 70px;
  }
  .card--front .wordmark { color: var(--red); font-size: 36px; text-align: left; }
  .front-mark {
    position: absolute; right: 38px; top: 40px;
    width: 180px; height: 180px; border-radius: 50%;
    background: radial-gradient(circle at 40% 40%, var(--red), var(--red-deep));
  }
  .person { position: absolute; left: 34px; top: 178px; }
  .person-name {
    font-family: "Michroma", Arial, sans-serif; color: var(--red);
    font-size: 17px; letter-spacing: 1px; text-transform: uppercase;
  }
  .person-title { font-size: 14px; margin-top: 2px; }
  .contacts { list-style: none; margin-top: 12px; font-size: 14px; line-height: 1.55; }
  .contacts li { display: flex; align-items: center; gap: 8px; }
  .contacts svg { width: 14px; height: 14px; flex: none; }
</style>
</head>
<body>
<main class="sheet">

  <section class="card card--back" aria-label="Card back">
    <div class="back-brand">
      <div class="brand-mark"></div>
      <div class="wordmark">Copperleaf<br>Roofing Co.</div>
    </div>
    <div class="divider"></div>
    <ul class="services">
      <li>Residential &amp; commercial roofing</li>
      <li>Roof Repairs &amp; Maintenance</li>
      <li>Storm Damage &amp; Insurance Claims specialist</li>
      <li>Christmas Lights and permanent Christmas lights</li>
      <li>Fencing. Windows. Gutters. Siding. Sheetrock, painting.</li>
    </ul>
  </section>

  <section class="card card--front" aria-label="Card front">
    <div class="front-brand">
      <div class="wordmark">Copperleaf<br>Roofing Co.</div>
    </div>
    <div class="front-mark"></div>
    <div class="person">
      <div class="person-name">Dale Mercer</div>
      <div class="person-title">Owner</div>
      <ul class="contacts">
        <li>
          <svg viewBox="0 0 16 16" aria-hidden="true"><circle cx="8" cy="8" r="8" fill="var(--red)"/><path d="M5 4.5l1.6-.4.9 2-1 .8a5 5 0 0 0 2.6 2.6l.8-1 2 .9-.4 1.6C8 11.5 4.5 8 5 4.5z" fill="#fff"/></svg>
          555-014-2290
        </li>
        <li>
          <svg viewBox="0 0 16 16" aria-hidden="true"><circle cx="8" cy="8" r="8" fill="var(--red)"/><rect x="4" y="5" width="8" height="6" fill="#fff"/><path d="M4 5l4 3.2L12 5" fill="none" stroke="var(--red)" stroke-width="1"/></svg>
          dale@copperleafroofing.co
        </li>
        <li>
          <svg viewBox="0 0 16 16" aria-hidden="true"><circle cx="8" cy="8" r="8" fill="var(--red)"/><circle cx="8" cy="8" r="4" fill="none" stroke="#fff" stroke-width="1.2"/><path d="M4 8h8M8 4c-2 2.5-2 5.5 0 8M8 4c2 2.5 2 5.5 0 8" fill="none" stroke="#fff" stroke-width="1"/></svg>
          www.copperleafroofing.co
        </li>
      </ul>
    </div>
  </section>

</main>
</body>
</html>
```